Willow Cradle Pregnancy and Baby Massage

I need a web design for a new business, WILLOW CRADLE PREGNANCY AND BABY MASSAGE that I am in the process of setting up in the suburbs of Perth, Western Australia. The business is owned and operated by myself and my intention is to service Pregnant Mothers and Parents of Young Babies that would benefit from massage. I would like to have a "Home Page" and pages for "About Me", "Pregnancy Massage", "Baby Massage", a Pricing Page for Pregnancy Massage Sessions, a Pricing Page for Baby Massage Sessions, and a "Contact Me" page to allow clients to either contact me with queries or book available pregnancy massage sessions on a particular day of the week. I would also like a "News" page that would include articles I have written, news about new courses and a link to my Facebook page (yet to be set up). I would like to keep the colour schemes similar to my logo design colours. I need the design to be easy to follow and to appeal to a younger audience (20's to mid 30's).
The target audience is pregnant mothers-to-be wishing to receive massage treatments, and new parents and grandparents of small babies that would like to learn how to massage their babies.
The look and feel should be modern, professional, elegant and feminine.
I need the design to be in a standard format such that I can update the content by myself ( and does not need specialised software) as the company and business progresses.

Target Market(s)

Contact Information for Business Card

Card should have rounded edges. Design should have the same "feel" as the website. Contact Details of my business address, mobile phone, email and website should be included.

Font styles to use
Script

Requirements
Must have
• Same colours as logo design. In cmyk system, the colours are: 20,60,0,0 which best result is pantone 681 and 40,40,0,0 which best result is pantone 2645. Card should include the logo design.

```html
<!DOCTYPE html>
<html lang="en">
<head>
<meta charset="utf-8">
<title>Willow Cradle – Contact</title>
<link rel="stylesheet" href="https://fonts.googleapis.com/css2?family=Belleza&family=Sue+Ellen+Francisco&display=swap">
<style>
  :root {
    --backdrop: #0d0d0d;
    --teal: #97bbb8;
    --blush: #ede3e3;
    --pink: #d54fa0;
    --lilac: #9a80c8;
    --ink: #3d4a47;
    --label: #1f2523;
    --field: #faf6f7;
  }
  * { margin: 0; padding: 0; box-sizing: border-box; }
  html, body { width: 1200px; height: 1025px; overflow: hidden; background: var(--backdrop); }
  .page {
    position: absolute; left: 289px; top: 0; width: 623px; height: 1021px;
    background: var(--blush); font-family: "Belleza", sans-serif; color: var(--ink);
  }
  .site-header {
    position: absolute; left: 0; top: 0; width: 100%; height: 72px; background: var(--teal);
  }
  .menu-icon { position: absolute; left: 21px; top: 27px; }
  .search-icon { position: absolute; left: 544px; top: 22px; }
  .brand {
    position: absolute; left: 0; width: 100%; top: 24px; text-align: center;
    font-family: "Belleza", sans-serif; font-size: 20px; color: var(--pink);
  }
  .breadcrumb {
    position: absolute; left: 48px; top: 97px; width: 100px; height: 24px;
    background: var(--teal); border-radius: 2px; color: var(--pink);
    font-family: "Sue Ellen Francisco", cursive; font-size: 15px; line-height: 24px; text-align: center;
  }
  .intro {
    position: absolute; left: 40px; width: 543px; top: 152px; text-align: center;
    font-size: 21px; line-height: 25.6px;
  }
  .form-title {
    position: absolute; left: 0; width: 100%; top: 362px; text-align: center;
    font-family: "Sue Ellen Francisco", cursive; font-size: 34px; color: var(--lilac);
  }
  .field-label { position: absolute; left: 25px; font-size: 20px; color: var(--label); }
  .field {
    position: absolute; left: 115px; width: 482px; height: 31px;
    background: var(--field); border-radius: 4px;
  }
  .field-message { height: 301px; border-radius: 6px; }
  .site-footer {
    position: absolute; left: 0; bottom: 0; width: 100%; height: 73px; background: var(--teal);
  }
  .social-dot {
    position: absolute; top: 23px; width: 26px; height: 26px; border-radius: 50%; background: var(--pink);
  }
</style>
</head>
<body>
<main class="page">
  <header class="site-header">
    <svg class="menu-icon" width="40" height="32" viewBox="0 0 40 32">
      <rect x="0" y="0" width="40" height="7" rx="3.5" fill="#d54fa0"/>
      <rect x="0" y="12.5" width="40" height="7" rx="3.5" fill="#d54fa0"/>
      <rect x="0" y="25" width="40" height="7" rx="3.5" fill="#d54fa0"/>
    </svg>
    <div class="brand">Willow Cradle</div>
    <svg class="search-icon" width="42" height="42" viewBox="0 0 42 42">
      <circle cx="16" cy="16" r="12" fill="none" stroke="#d54fa0" stroke-width="4"/>
      <line x1="25" y1="25" x2="38" y2="38" stroke="#d54fa0" stroke-width="6" stroke-linecap="round"/>
    </svg>
  </header>

  <div class="breadcrumb">Home &lt; Contact</div>

  <p class="intro">
    To contact Maren, or to book a session, please use the details below, or submit the contact form.<br>
    Maren Ellery<br>
    Willow Cradle Pregnancy and Infant Massage<br>
    Email maren.ellery@willow-cradle.com.au<br>
    Telephone&nbsp; 041 5550 382
  </p>

  <h2 class="form-title">Contact Form</h2>

  <span class="field-label" style="top:426px">Name</span>
  <div class="field" style="top:424px"></div>
  <span class="field-label" style="top:477px">Email</span>
  <div class="field" style="top:472px"></div>
  <span class="field-label" style="top:528px">Phone</span>
  <div class="field" style="top:523px"></div>
  <span class="field-label" style="top:604px">Message</span>
  <div class="field field-message" style="top:596px"></div>

  <footer class="site-footer">
    <span class="social-dot" style="left:58px"></span>
    <span class="social-dot" style="left:174px"></span>
    <span class="social-dot" style="left:290px"></span>
    <span class="social-dot" style="left:410px"></span>
    <span class="social-dot" style="left:543px"></span>
  </footer>
</main>
</body>
</html>
```